Income Tax and Accounting Brochure

I need a brochure using my new logo (file attached). I do tax work and accounting work. I am an EA (QFB Enrolled Agent - logo attached) and would like this incorporated into the brochure. I also have a MSA in Accounting. Please incorporate the text that I have provided in the brochure.
Updates

Need extra days to review

Target Market(s)

Tax Clients - both business and individuals

Industry/Entity Type

Accounting

Colors
0054AA
0677BA
7BADD7
CADEEF
E8F1F8

Requirements
Must have
• Use my logo and the QFB EA file in the brochure
Nice to have
• I would like to see a brochure that I can customize with my own text if possible.

```html
<!DOCTYPE html>
<html lang="en">
<head>
<meta charset="utf-8">
<title>Harborline Tax &amp; Advisory – Income Tax and Business Consulting</title>
<link href="https://fonts.googleapis.com/css2?family=Poppins:wght@300;500;600&display=swap" rel="stylesheet">
<style>
  :root{
    --brand-blue:#0054AA;
    --brand-sky:#0677BA;
    --brand-light:#7BADD7;
    --brand-pale:#CADEEF;
    --brand-mist:#E8F1F8;
    --ink:#111111;
    --paper:#ffffff;
  }
  *{margin:0;padding:0;box-sizing:border-box}
  html,body{width:847px;height:1200px;overflow:hidden;background:var(--paper)}
  body{font-family:'Poppins',sans-serif;color:var(--ink)}
  .brochure{position:relative;width:847px;height:1200px;overflow:hidden;background:var(--paper)}
  .hero-art{position:absolute;left:0;top:0}
  .brand-name{position:absolute;display:flex;align-items:center;gap:8px;
    font-weight:600;color:var(--brand-blue);letter-spacing:.02em;line-height:1.15}
  .brand-name .mark{width:44px;height:44px;border-radius:50%;background:var(--brand-blue);flex:none}
  .brand-top{left:14px;top:14px;font-size:15px}
  .brand-bottom{left:612px;top:1106px;font-size:15px}
  .hero-title{position:absolute;left:22px;top:178px;color:#fff;font-weight:300;font-size:33px;line-height:37px}
  .hero-title strong{font-weight:600}
  .content{position:absolute;left:36px;width:740px}
  h2{font-weight:600;font-size:22px;line-height:1.2}
  h3{font-weight:500;font-size:17px;line-height:1.2}
  h4{font-weight:600;font-size:19px;line-height:1.2}
  p,li{font-weight:500;font-size:11px}
  .about{top:420px}
  .about p{line-height:13.3px;margin-top:22px;width:710px}
  .about p+p{margin-top:13px}
  .joy{top:590px}
  .joy h3{margin-top:10px}
  .joy p{line-height:17.6px;margin-top:4px;width:700px}
  .joy p+p{margin-top:0}
  .benefits{top:783px}
  .benefits ul{list-style:none;margin-top:14px}
  .benefits li{line-height:17.6px;padding-left:13px;position:relative;width:740px}
  .benefits li::before{content:"•";position:absolute;left:0;font-size:8px}
  .books{top:979px}
  .books p{margin-top:22px;line-height:17.6px;width:640px}
  .ea-badge{position:absolute;left:424px;top:1116px;width:72px;height:42px;
    border:4px solid var(--brand-light);background:var(--brand-mist)}
</style>
</head>
<body>
<div class="brochure">
  <svg class="hero-art" width="847" height="520" viewBox="0 0 847 520">
    <defs>
      <linearGradient id="heroTone" x1="0" y1="0" x2="1" y2="1">
        <stop offset="0" stop-color="#55575c"/>
        <stop offset=".5" stop-color="#6b5a4c"/>
        <stop offset="1" stop-color="#4a4b50"/>
      </linearGradient>
    </defs>
    <rect width="847" height="520" fill="url(#heroTone)" role="img" aria-label="Photo of a smiling tax advisor shaking hands with clients across a desk"/>
    <path d="M0,0 H385 C300,70 150,112 0,112 Z" fill="var(--brand-sky)"/>
    <path d="M0,0 H360 C280,62 140,104 0,106 Z" fill="var(--paper)"/>
    <path d="M0,386 Q430,290 847,465 V520 H0 Z" fill="var(--brand-blue)"/>
    <path d="M0,414 Q430,318 847,498 V520 H0 Z" fill="var(--paper)"/>
  </svg>

  <div class="brand-name brand-top"><span class="mark"></span><span>HARBORLINE TAX<br>&amp; ADVISORY, LLC</span></div>

  <h1 class="hero-title">Income Tax and<br>Buisness <strong>Consulting</strong></h1>

  <section class="content about">
    <h2>About Marian J Colter, MSA EA (Principal)</h2>
    <p>I have a Masters' Degree in accounting and am an QFB Enrolled Agent. I am also a LedgerLane Advanced Certified Consultant in both the online and desktop products including Enterprise and Point of Sale. I provide individual and small business tax services, Accounting, bookkeeping, QFB representation, insurance audit representation, business license assistance and more.</p>
    <p>I have experience working with a wide variety of clients from the point where they first decide they want to start a business. They are often unsure about what to do first- I have a lot of experience to offer you.</p>
  </section>

  <section class="content joy">
    <h2>What a joy it is to watch success in action!</h2>
    <h3>Tax Preparation – why hire us?</h3>
    <p>Preparing your own income tax return can be a task that leaves you with more questions than answers. According to a study released by the National Revenue Research Office last year, most taxpayers (77% of 71 million taxpayers) believe they benefited from using a professional tax preparer.</p>
    <p>Whether we like it or not, today's tax laws are so complicated that filing a relatively simple return can be confusing. It is just too easy to overlook deductions and credits to which you are entitled. Even if you use a computer software program there's no substitute for the assistance of an experienced tax professional.</p>
  </section>

  <section class="content benefits">
    <h4>Here's what your get...</h4>
    <ul>
      <li>Your tax return will be checked and rechecked by our computer software identifying potential problems the QFB may look at more closely and reviewing the math to limit QFB contacts.</li>
      <li>Your tax return can be filed electronically so you will get a refund back quicker.</li>
      <li>Our staff will show you how to adjust your payroll withholding to get more money back each week. Why give the QFB an interest free loan for up to 16 months.</li>
      <li>We will show you potential deductions to limit your tax liability for next year. In addition, we will give you a sheet of commonly overlooked deductions to limit the following year's tax liability.</li>
    </ul>
  </section>

  <section class="content books">
    <h4>Books a Mess: No Problem!</h4>
    <p>If you own a small business and haven't kept up your bookkeeping, don't worry. We can help you. We'll prepare your bookkeeping for the year, prepare a full Schedule C, as well as your personal income tax return. Then we'll help you set up an easy system that allows you to keep your books in tip-top shape next year.</p>
  </section>

  <div class="ea-badge" role="img" aria-label="Enrolled agent credential badge"></div>
  <div class="brand-name brand-bottom"><span class="mark"></span><span>HARBORLINE TAX<br>&amp; ADVISORY, LLC</span></div>
</div>
</body>
</html>
```